Realty Group Needs Classy, Contemporary Letterhead Design

We need a letterhead design for a new realty company located in NY, USA. We buy investment properties to rehabilitate and or keep in our rental portfolio.

```html
<!DOCTYPE html>
<html lang="en">
<head>
<meta charset="utf-8">
<title>Meridale Realty Group — Letterhead</title>
<link rel="stylesheet" href="https://fonts.googleapis.com/css2?family=Montserrat:wght@800&family=Open+Sans:wght@400;700&display=swap">
<style>
  :root {
    --backdrop: #e9e9ea;
    --paper: #ffffff;
    --brand-purple: #55299a;
    --brand-gray: #7d7d7f;
    --text-gray: #6e6e70;
  }
  * { margin: 0; padding: 0; box-sizing: border-box; }
  html, body {
    width: 1200px; height: 795px; overflow: hidden;
    background: var(--backdrop);
  }
  .letterhead {
    position: absolute;
    left: 331px; top: 17px;
    width: 537px; height: 760px;
    background: var(--paper);
    box-shadow: 0 4px 18px rgba(0,0,0,0.12);
    overflow: hidden;
  }
  .header-swoosh {
    position: absolute; left: 0; top: 0;
    width: 537px; height: 300px;
  }
  .swoosh-purple { fill: var(--brand-purple); }
  .swoosh-gray { fill: var(--brand-gray); }
  .brand {
    position: absolute; left: 30px; top: 160px;
    font-family: "Montserrat", sans-serif;
    font-weight: 800;
    color: var(--brand-purple);
    line-height: 1;
  }
  .brand-name { font-size: 23px; letter-spacing: 0.3px; }
  .brand-tagline { font-size: 7.5px; letter-spacing: 1.2px; margin-top: 4px; text-align: right; }
  .footer-contact {
    position: absolute; right: 30px; bottom: 30px;
    text-align: right;
    font-family: "Open Sans", sans-serif;
    font-style: normal;
    font-size: 8.5px;
    line-height: 1.6;
    color: var(--text-gray);
  }
  .contact-company { font-weight: 700; color: var(--brand-purple); font-size: 9px; }
  .contact-row { display: flex; justify-content: flex-end; align-items: center; gap: 4px; }
  .contact-icon { width: 9px; height: 9px; flex: none; }
  .contact-icon circle { fill: var(--brand-purple); }
  .contact-icon path { fill: none; stroke: #fff; stroke-width: 1.2; stroke-linecap: round; stroke-linejoin: round; }
  .contact-web { color: var(--brand-purple); }
  .footer-band {
    position: absolute; left: 0; right: 0; bottom: 0;
    height: 10px; background: var(--brand-purple);
  }
</style>
</head>
<body>
  <main class="letterhead">
    <svg class="header-swoosh" viewBox="0 0 537 300" aria-hidden="true">
      <path class="swoosh-gray" d="M352,0 L398,0 C322,22 300,110 250,172 C200,232 110,244 0,250 L0,241 C108,236 190,222 236,166 C282,110 302,22 352,0 Z"/>
      <path class="swoosh-purple" d="M300,0 L346,0 C272,26 258,118 218,166 C208,178 200,186 190,194 C206,172 218,150 228,126 C244,86 258,28 300,0 Z"/>
    </svg>

    <div class="brand">
      <div class="brand-name">MERIDALE</div>
      <div class="brand-tagline">REALTY GROUP, LLC</div>
    </div>

    <address class="footer-contact">
      <div class="contact-company">Meridale Realty Group, LLC</div>
      <div>Suite 102 Street name, State, Zip 2034, Country</div>
      <div class="contact-row">
        <svg class="contact-icon" viewBox="0 0 10 10" aria-hidden="true"><circle cx="5" cy="5" r="5"/><path d="M3.4,2.8 L4.2,4.6 L3.8,5 C4.2,5.8 4.8,6.3 5.2,6.4 L5.6,6 L7.2,6.8"/></svg>
        <span>(00) 01234 567 890</span>
        <svg class="contact-icon" viewBox="0 0 10 10" aria-hidden="true"><circle cx="5" cy="5" r="5"/><path d="M3,3.5 H7 V6.5 H3 Z"/></svg>
        <span>(00) 01234 567 891</span>
        <svg class="contact-icon" viewBox="0 0 10 10" aria-hidden="true"><circle cx="5" cy="5" r="5"/><path d="M2.8,3.4 H7.2 V6.6 H2.8 Z M2.8,3.4 L5,5.2 L7.2,3.4"/></svg>
        <span>hello@meridalerealty.com</span>
      </div>
      <div class="contact-web">www.meridalerealty.com</div>
    </address>

    <div class="footer-band"></div>
  </main>
</body>
</html>
```